Kestrelbrook Student Accomodation needs a business card design

Hi Guys,

We are a Student Accommodation company in Australia. We already have a logo which I will submit.

I will require the design of the business cards from you.

I am after something that looks clean, modern and that people feel interested and actually want to contact us.

We would like to see designs that are innovative.

On the business cards I will require to have:

Employee Name
Position
Phone number
Email
/kestrelbrook page

I hope you can help me with this project guys as I have heard really good things from you.

```html
<!DOCTYPE html>
<html lang="en">
<head>
<meta charset="utf-8">
<title>Kestrelbrook Student Accomodation – Business Card</title>
<link href="https://fonts.googleapis.com/css2?family=Exo+2:wght@400;600;800&display=swap" rel="stylesheet">
<style>
  :root {
    --bg: #d9d9d9;
    --card: #fbfbfb;
    --green: #1e9a2e;
    --orange: #f2a516;
    --ink: #3a3a3a;
  }
  * { box-sizing: border-box; margin: 0; padding: 0; }
  html, body { width: 1200px; height: 947px; overflow: hidden; }
  body {
    background: radial-gradient(ellipse at 50% 40%, #ececec, var(--bg));
    font-family: "Exo 2", sans-serif;
    position: relative;
  }
  .card {
    position: absolute;
    top: 183px;
    width: 340px;
    height: 580px;
    background: var(--card);
    border-radius: 22px;
    box-shadow: 0 14px 30px rgba(0,0,0,.18);
  }
  .card--back { left: 220px; }
  .card--front { left: 640px; }

  .logo { position: absolute; display: flex; align-items: flex-end; }
  .logo__art {
    width: 84px; height: 80px; border-radius: 6px; flex: none;
    background: linear-gradient(135deg, var(--orange) 0 50%, var(--green) 50% 100%);
  }
  .logo__name {
    margin-left: 8px; margin-bottom: 22px;
    font-weight: 800; font-size: 16px; line-height: 1.05;
    color: var(--green); text-transform: uppercase; letter-spacing: .4px;
  }
  .card--back .logo { left: 56px; top: 240px; }

  .social { position: absolute; right: 24px; bottom: 24px; display: flex; gap: 16px; }
  .social__item { display: flex; align-items: center; gap: 5px; font-size: 11px; }
  .social__mark { width: 12px; height: 12px; border-radius: 2px; }
  .social__item--one { color: var(--orange); }
  .social__item--one .social__mark { background: var(--orange); }
  .social__item--two { color: var(--green); }
  .social__item--two .social__mark { background: var(--green); }

  .card--front .logo { left: 36px; top: 60px; }

  .contacts { position: absolute; left: 36px; top: 236px; right: 24px; list-style: none; }
  .contact { display: flex; align-items: center; margin-bottom: 40px; }
  .contact__icon { width: 34px; height: 34px; margin-right: 14px; flex: none; }
  .contact__bar { width: 4px; align-self: stretch; min-height: 40px; background: var(--ink); margin-right: 12px; flex: none; }
  .contact__text { font-size: 14px; color: var(--ink); line-height: 1.4; letter-spacing: .4px; }
  .person__name { color: var(--orange); font-weight: 600; font-size: 20px; letter-spacing: 1px; text-transform: uppercase; line-height: 1.2; }
  .person__role { color: var(--ink); font-size: 12px; letter-spacing: .8px; }
</style>
</head>
<body>

<section class="card card--back" aria-label="Card back">
  <div class="logo">
    <div class="logo__art" role="img" aria-label="Logo illustration: orange buildings over a green map of Australia"></div>
    <div class="logo__name">Kestrelbrook<br>Student<br>Accomodation</div>
  </div>
  <div class="social">
    <span class="social__item social__item--one"><span class="social__mark"></span>/kestrelbrook</span>
    <span class="social__item social__item--two"><span class="social__mark"></span>@kestrelbrook</span>
  </div>
</section>

<section class="card card--front" aria-label="Card front">
  <div class="logo">
    <div class="logo__art" role="img" aria-label="Logo illustration: orange buildings over a green map of Australia"></div>
    <div class="logo__name">Kestrelbrook<br>Student<br>Accomodation</div>
  </div>

  <ul class="contacts">
    <li class="contact">
      <svg class="contact__icon" viewBox="0 0 36 36" aria-hidden="true">
        <circle cx="18" cy="11" r="7" fill="var(--green)"/>
        <path d="M5 33c0-8 6-13 13-13s13 5 13 13z" fill="var(--green)"/>
      </svg>
      <span class="contact__bar"></span>
      <div class="person">
        <p class="person__name">Marcus Whitfield</p>
        <p class="person__role">Managing Director</p>
      </div>
    </li>
    <li class="contact">
      <svg class="contact__icon" viewBox="0 0 36 36" aria-hidden="true">
        <path d="M18 2c-7 0-12 5-12 12 0 9 12 20 12 20s12-11 12-20c0-7-5-12-12-12z" fill="var(--green)"/>
        <circle cx="18" cy="14" r="4.5" fill="var(--card)"/>
      </svg>
      <span class="contact__bar"></span>
      <p class="contact__text">42 Level 5 Harbour Walk<br>Road, Sydney NSW</p>
    </li>
    <li class="contact">
      <svg class="contact__icon" viewBox="0 0 36 36" aria-hidden="true">
        <circle cx="18" cy="18" r="15" fill="var(--green)"/>
        <g fill="none" stroke="var(--card)" stroke-width="1.6">
          <ellipse cx="18" cy="18" rx="6.5" ry="15"/>
          <line x1="3" y1="18" x2="33" y2="18"/>
          <line x1="18" y1="3" x2="18" y2="33"/>
          <path d="M6 10h24M6 26h24"/>
        </g>
      </svg>
      <span class="contact__bar"></span>
      <p class="contact__text">012 555 0184<br>hello@kestrelbrook.au<br>kestrelbrook.au</p>
    </li>
  </ul>
</section>

</body>
</html>
```